Tovin Brightway Website Design

About The Client:
Tovin Brightway is a sugar-free foods chain store providing services to Diabetics. They focus on the China domestic market. They describe themselves as being the 3rd space for Diabetics, the space between hospital and the home that help improve the quality of life for people wit Diabetes (see attached infographics).

They regularly hold education and advice events throughout the China. Tovin Brightway distribute a wide product range of food that is suitable for diabetic people. Tovin Brightway operate as a Franchise, providing business development services and Industry knowledge. They are actively seeking business partnerships at present.

The Brief:
Design a Home page and secondary information page(PSD only no code) that communicates our company services and company philosophy(3rd Space).
The final design should communicate 'Health, Social Responsibility and Professionalism'.
Colour scheme should orientate around Blue and White, see attached logo.

Websites we like:

http://lumo.vextaran.com/home/

https://www.pondrelix.com/

http://gate.zt.com/

Hello all, the client has advised us that he want to display the professional advice service available for diabetic people more so than a food distributor. The client is also hoping to use his website as a marketing platform to attract affiliates and build partnerships as part of Tovin Brightway's business expansion strategy.

So can you make the page more corporate, reliable and professional. Use images of experts/doctors interacting with patients and also training/knowledge transfer images.

Thanks

Hello all, could you include stock images of both Chinese and Caucasians

Yeaahhh, Infographics and photos have been uploaded. Feel free to use them in your designs and also as references.

Target Market(s)

The target market is Chinese B2B in the Diabetics industry and Entrepreneurs looking to cooperate with Tovin Brightway.

Industry/Entity Type

Education

Requirements
Must have
• menu navigation with 7-8 sections,
a full screen background image,
Social Media icons,
Logo in top left,
Site search.
Nice to have
• The website must be clear and easy to use, less complicated.

See attached files of some Tovin Brightway infographics. Feel free to include elements of these into the design.
Should not have
• Should not use stock images of people from any other country, the client wants stock images of Chinese people only. Avoid photos showing obesity.

```html
<!DOCTYPE html>
<html lang="en">
<head>
<meta charset="utf-8">
<title>Tovin Brightway</title>
<link rel="stylesheet" href="https://fonts.googleapis.com/css2?family=Open+Sans:ital,wght@0,400;0,600;0,700;1,400&family=PT+Sans:wght@400;700&family=PT+Sans+Narrow:wght@400;700&display=swap">
<style>
:root{
  --blue:#1a9fe3;
  --blue-light:#3db5ec;
  --blue-band:#4bb8ee;
  --blue-head:#1b78bf;
  --red:#d0151e;
  --red-dark:#b80e16;
  --ink:#222;
  --text:#444;
  --muted:#666;
  --rule:#e4e4e4;
  --dark-btn:#404040;
  --footer:#575757;
  --footer-text:#e6e6e6;
}
*{margin:0;padding:0;box-sizing:border-box}
html,body{width:1043px;height:1200px;overflow:hidden;background:#fff}
body{font-family:"Open Sans",sans-serif;color:var(--text)}
.page{position:relative;width:1200px;height:1380px;transform:scale(0.869167);transform-origin:0 0;overflow:hidden;background:#fff}
.abs{position:absolute}
.topline{left:0;top:0;width:1200px;height:6px;background:var(--blue)}

/* header */
.brand{left:182px;top:20px;display:flex;flex-direction:column;gap:10px}
.brand-mark{width:62px;height:62px;background:var(--blue)}
.brand-name{font-family:"Open Sans",sans-serif;font-size:20px;color:var(--blue);font-weight:400;white-space:nowrap}
.search{left:678px;top:40px;width:173px;height:21px;display:flex}
.search-field{flex:1;border:1px solid #ddd;background:#f7f7f7;font:italic 12px "Open Sans",sans-serif;color:#888;padding:2px 10px}
.search-btn{width:29px;background:var(--red);display:flex;align-items:center;justify-content:center}
.lang{left:872px;top:39px;width:153px;height:22px;border:1px solid #ccc;display:flex;align-items:center;padding:0 9px;gap:8px;font:italic 12px "Open Sans",sans-serif;color:#999}
.lang-flag{width:19px;height:12px;background:#2b4a8b}
.lang svg{margin-left:auto}
.nav{left:559px;top:92px;display:flex;align-items:center;height:42px}
.nav a{font:600 14px "Open Sans",sans-serif;color:var(--ink);text-decoration:none;margin-right:33px;line-height:42px}
.nav a.active{background:linear-gradient(#e01d26,var(--red-dark));color:#fff;padding:0 20px;border-radius:3px;margin-right:19px}

/* hero */
.hero{left:0;top:147px;width:1200px;height:355px;background:var(--blue)}
.hero-photo{left:720px;top:147px;width:270px;height:355px;background:linear-gradient(180deg,rgba(26,159,227,0) 0%,rgba(214,58,48,.55) 30%,#d3281f 60%,#c41a1a 100%)}
.hero-title{left:170px;top:225px;height:48px;padding:0 17px;background:var(--blue-band);font:700 23px/48px "PT Sans",sans-serif;color:#fff;white-space:nowrap}
.hero-text{left:182px;top:285px;width:515px;font:14px/21px "PT Sans",sans-serif;color:#fff}
.btn-more{left:183px;top:414px;width:115px;height:44px;background:linear-gradient(#d8141e,#bd0d16);border-radius:3px;color:#fff;font:400 18px/44px "PT Sans",sans-serif;text-align:center}
.hero-arrow{top:308px}

/* welcome */
.welcome-bg{left:155px;top:503px;width:820px;height:287px;background:linear-gradient(90deg,rgba(245,245,245,0),#f7f7f7 15%,#f7f7f7 85%,rgba(245,245,245,0));box-shadow:0 8px 12px -10px rgba(0,0,0,.15)}
.hero-shadow{left:150px;top:502px;width:900px;height:14px;background:radial-gradient(ellipse at 50% 0,rgba(0,0,0,.18),transparent 70%)}
h2{font:700 21px "PT Sans Narrow",sans-serif;text-transform:uppercase;white-space:nowrap}
h2 em{font-style:normal;color:var(--red)}
.h-dark{color:var(--ink)}
.h-blue{color:var(--blue-head)}
.h-foot{color:var(--blue-light)}
.rule{height:1px;background:var(--rule)}
.lead{left:165px;top:593px;font:700 12.5px "Open Sans",sans-serif;color:var(--ink)}
.body-copy{font:11px/18px "Open Sans",sans-serif;color:#333;text-align:justify}
.btn{position:absolute;font:400 15px "PT Sans Narrow",sans-serif;color:#fff;text-align:center}
.btn-dark{background:var(--dark-btn);height:32px;line-height:32px}
.btn-blue{background:var(--blue-light);height:32px;line-height:32px}
.pager{display:flex;gap:9px}
.pager span{width:12px;height:12px;background:#333;display:flex;align-items:center;justify-content:center}
.product-photo{left:776px;top:586px;width:263px;height:99px;border:1px solid #ccc;background:linear-gradient(90deg,#e9eef5,#d3dff0 30%,#f2f2f2 50%,#cfd9ec 75%,#eef1f6)}
.small-copy{font:11px/14px "Open Sans",sans-serif;color:var(--muted);text-align:left}

/* row three */
.avatar{width:74px;height:74px;border-radius:50%}
.tips{left:503px;top:876px;width:228px;list-style:none}
.tips li{display:flex;gap:8px;height:41px}
.tips li i{flex:none;width:11px;height:11px;margin-top:2px;background:var(--blue-head);display:flex;align-items:center;justify-content:center}
.date{width:58px;height:58px;border-radius:50%;background:var(--blue-light);color:#fff;font:11px/58px "Open Sans",sans-serif;text-align:center}

/* footer */
.footer-wave{left:0;top:1108px}
.footer{left:0;top:1170px;width:1200px;height:210px;background:var(--footer)}
.foot-rule{height:1px;background:#7a7a7a}
.foot-copy{font:11px/16px "Open Sans",sans-serif;color:var(--footer-text);text-align:left}
.doctor{left:166px;top:1243px;width:70px;height:68px;background:linear-gradient(#d9d3cc,#b9aea4)}
.email{left:512px;top:1282px;width:258px;height:31px;background:#fff;border:1px solid #ccc;border-radius:3px;font:italic 11px/29px "Open Sans",sans-serif;color:#888;padding-left:15px}
.social{left:833px;top:1201px;display:flex;gap:12px}
.social span{width:26px;height:26px}
.copyright{left:780px;top:1247px;width:278px;text-align:right;font:11px "Open Sans",sans-serif;color:var(--footer-text);white-space:nowrap}
</style>
</head>
<body>
<div class="page">
  <div class="abs topline"></div>

  <header>
    <div class="abs brand">
      <div class="brand-mark"></div>
      <div class="brand-name">Tovin Brightway</div>
    </div>
    <div class="abs search">
      <div class="search-field">Search</div>
      <div class="search-btn">
        <svg width="13" height="13" viewBox="0 0 13 13"><circle cx="5.5" cy="5.5" r="4" fill="none" stroke="#fff" stroke-width="2"/><line x1="8.5" y1="8.5" x2="12" y2="12" stroke="#fff" stroke-width="2.2"/></svg>
      </div>
    </div>
    <div class="abs lang">
      <span class="lang-flag"></span>English
      <svg width="8" height="6" viewBox="0 0 8 6"><path d="M1 1l3 3 3-3" fill="none" stroke="#333" stroke-width="1.5"/></svg>
    </div>
    <nav class="abs nav">
      <a class="active" href="#">HOME</a>
      <a href="#">ABOUT</a>
      <a href="#">SERVICES</a>
      <a href="#">TESTIMONIALS</a>
      <a href="#">CONTACT</a>
    </nav>
  </header>

  <section class="abs hero"></section>
  <div class="abs hero-photo" role="img" aria-label="Photo of a smiling woman in a red qipao dress"></div>
  <h1 class="abs hero-title">SPECIALIST FOOD TOVIN BRIGHTWAY INFORMATION</h1>
  <p class="abs hero-text">Cum sociis natoque penatibus et magnis dis parturient montes, nascetur ridiculus mus. In iaculis facilisis massa. Etiam eu urna.&nbsp; In iaculis facilisis massa. Etiam eu urna. Sed porta.Cum sociis natoque penatibus et magnis dis parturient montes, nascetur ridiculus mus. In iaculis facilisis massa. Etiam eu urna.&nbsp; In iaculis facilisis massa. Etiam eu urna. Sed porta.</p>
  <div class="abs btn-more">MORE</div>
  <svg class="abs hero-arrow" style="left:84px" width="18" height="48" viewBox="0 0 18 48"><path d="M14 2 L5 24 L14 46" fill="none" stroke="#fff" stroke-width="3.5"/></svg>
  <svg class="abs hero-arrow" style="left:1095px" width="18" height="48" viewBox="0 0 18 48"><path d="M4 2 L13 24 L4 46" fill="none" stroke="#fff" stroke-width="3.5"/></svg>

  <div class="abs welcome-bg"></div>
  <div class="abs hero-shadow"></div>

  <section>
    <h2 class="abs h-dark" style="left:165px;top:541px">Welcome to <em>Tovin Brightway</em></h2>
    <div class="abs rule" style="left:165px;top:577px;width:565px"></div>
    <p class="abs lead">Mauris vel lacus vitae felis vestibulum volutpat. Etiam est nunc, venisl.</p>
    <p class="abs body-copy" style="left:166px;top:619px;width:566px">Sed ut perspiciatis unde omnis iste natus error sit voluptatem accusantium doloremque laudantium, totam rem aperiam, eaque ipsa quae ab illo inventore veritatis et quasi architecto beatae vitae dicta sunt explicabo. Nemo enim ipsam voluptatem quia voluptas sit aspernatur aut odit aut fugit, sed quia consequuntur magni dolores eos qui ratione voluptatem sequi nesciunt. Neque porro quisquam est, qui dolorem ipsum quia dolor sit amet.Sed ut perspiciatis unde omnis iste natus error sit voluptatem accusantium doloremque.</p>
    <div class="btn btn-dark" style="left:648px;top:723px;width:81px">learn more</div>

    <h2 class="abs h-dark" style="left:776px;top:545px;font-size:18px">Diabeties <em>Product</em></h2>
    <div class="abs pager" style="left:1009px;top:548px">
      <span><svg width="6" height="6" viewBox="0 0 6 6"><path d="M5 0v6L1 3z" fill="#fff"/></svg></span>
      <span><svg width="6" height="6" viewBox="0 0 6 6"><path d="M1 0v6l4-3z" fill="#fff"/></svg></span>
    </div>
    <div class="abs rule" style="left:776px;top:577px;width:266px"></div>
    <div class="abs product-photo" role="img" aria-label="Assorted diabetes care product boxes and bottles"></div>
    <p class="abs body-copy" style="left:780px;top:690px;width:260px;font-size:11px;line-height:16px">Sed ut perspiciatis unde omnis iste natus error sit voluptatem accusantium doloremque laudantium, totam rem aperiam</p>
    <div class="btn btn-dark" style="left:963px;top:729px;width:80px">learn more</div>
  </section>

  <section>
    <h2 class="abs h-blue" style="left:183px;top:823px">Testimonials</h2>
    <div class="abs rule" style="left:175px;top:861px;width:277px"></div>
    <div class="abs avatar" style="left:174px;top:878px;background:linear-gradient(120deg,#e06a3a,#6b5040 55%,#2a2a2a)" role="img" aria-label="Portrait of a smiling man"></div>
    <p class="abs small-copy" style="left:256px;top:886px;width:193px">Sed ut perspiciatis unde omnis iste natus error sit voluptatem accusan-tium doloremque rem aperiam, eaque ipsa quae ab illo inven.</p>
    <div class="abs avatar" style="left:174px;top:968px;background:linear-gradient(150deg,#3a3030,#c9a08a 55%,#e8d8cc)" role="img" aria-label="Portrait of a smiling woman"></div>
    <p class="abs small-copy" style="left:256px;top:977px;width:193px">Sed ut perspiciatis unde omnis iste natus error sit voluptatem accusan-tium doloremque rem aperiam, eaque ipsa quae ab illo inven.</p>
    <div class="btn btn-blue" style="left:368px;top:1044px;width:80px">learn more</div>

    <h2 class="abs h-blue" style="left:504px;top:823px">Tips for Diabeties</h2>
    <div class="abs rule" style="left:497px;top:861px;width:240px"></div>
    <ul class="abs tips small-copy">
      <li><i><svg width="5" height="6" viewBox="0 0 5 6"><path d="M0 0v6l5-3z" fill="#fff"/></svg></i>Sed ut perspiciatis unde omnis iste natus error accusantium doloremque</li>
      <li><i><svg width="5" height="6" viewBox="0 0 5 6"><path d="M0 0v6l5-3z" fill="#fff"/></svg></i>Sed ut perspiciatis unde omnis iste natus error accusantium doloremque</li>
      <li><i><svg width="5" height="6" viewBox="0 0 5 6"><path d="M0 0v6l5-3z" fill="#fff"/></svg></i>Sed ut perspiciatis unde omnis iste natus error accusantium doloremque</li>
      <li><i><svg width="5" height="6" viewBox="0 0 5 6"><path d="M0 0v6l5-3z" fill="#fff"/></svg></i>Sed ut perspiciatis unde omnis iste natus error accusantium doloremque</li>
    </ul>
    <div class="btn btn-blue" style="left:645px;top:1044px;width:81px">learn more</div>

    <h2 class="abs h-blue" style="left:784px;top:823px">Latest News</h2>
    <div class="abs pager" style="left:1009px;top:829px">
      <span><svg width="6" height="6" viewBox="0 0 6 6"><path d="M5 0v6L1 3z" fill="#fff"/></svg></span>
      <span><svg width="6" height="6" viewBox="0 0 6 6"><path d="M1 0v6l4-3z" fill="#fff"/></svg></span>
    </div>
    <div class="abs rule" style="left:777px;top:861px;width:275px"></div>
    <div class="abs date" style="left:782px;top:885px">July 22</div>
    <p class="abs small-copy" style="left:849px;top:886px;width:192px">Sed ut perspiciatis unde omnis iste natus error sit voluptatem accusan-tium doloremque rem aperiam, eaque ipsa quae ab illo inven.</p>
    <div class="abs date" style="left:782px;top:966px">July 22</div>
    <p class="abs small-copy" style="left:849px;top:967px;width:192px">Sed ut perspiciatis unde omnis iste natus error sit voluptatem accusan-tium doloremque rem aperiam, eaque ipsa quae ab illo inven.</p>
    <div class="btn btn-blue" style="left:968px;top:1044px;width:81px">learn more</div>
  </section>

  <svg class="abs footer-wave" width="1200" height="70" viewBox="0 0 1200 70">
    <path d="M0 44 C300 68 600 58 900 24 C1010 12 1110 8 1200 10 V70 H0 Z" fill="var(--blue-light)"/>
    <path d="M0 52 C300 74 600 66 900 34 C1010 22 1110 20 1200 22 V70 H0 Z" fill="#fff" opacity=".9"/>
    <path d="M0 55 C300 76 600 70 900 40 C1010 30 1110 28 1200 28 V70 H0 Z" fill="var(--footer)"/>
  </svg>
  <footer class="abs footer"></footer>

  <h2 class="abs h-foot" style="left:168px;top:1194px">Doctor's Advices</h2>
  <div class="abs foot-rule" style="left:166px;top:1225px;width:253px"></div>
  <div class="abs doctor" role="img" aria-label="Portrait of a female doctor in a white coat"></div>
  <p class="abs foot-copy" style="left:247px;top:1242px;width:180px">Sed ut perspiciatis unde omnis iste natus error sit voluptatem accusan-tium doloremque laudantium, totam rem aperiam,</p>
  <div class="btn btn-blue" style="left:354px;top:1310px;width:69px;height:28px;line-height:28px;font:12px/28px 'Open Sans',sans-serif;border-radius:3px">More &gt;&gt;</div>

  <h2 class="abs h-foot" style="left:515px;top:1194px">Newsletter</h2>
  <div class="abs foot-rule" style="left:512px;top:1225px;width:258px"></div>
  <p class="abs foot-copy" style="left:514px;top:1231px;width:256px;color:#d8d8d8;line-height:18px">Sed ut perspiciatis unde omnis iste natus error sit voluptatem accusantium doloremque la.</p>
  <div class="abs email">Your Email Id</div>
  <div class="btn btn-blue" style="left:665px;top:1331px;width:104px;font-size:16px">Subscribe</div>

  <div class="abs social" aria-label="Social media links">
    <span style="background:#3b5a9a"></span>
    <span style="background:#35b3e8"></span>
    <span style="background:#333"></span>
    <span style="background:#f29222"></span>
    <span style="background:#c4161c"></span>
    <span style="background:#8fa3b0;display:flex;align-items:center;justify-content:center"><svg width="16" height="11" viewBox="0 0 16 11"><rect x=".5" y=".5" width="15" height="10" fill="none" stroke="#fff"/><path d="M.5 .5l7.5 6 7.5-6" fill="none" stroke="#fff"/></svg></span>
  </div>
  <p class="abs copyright">© 2013 TovinBrightway.com., All rights reserved</p>
</div>
</body>
</html>
```